VeraMosk Powerpoint design

We've recently redesigned our logos and would like a single presentation format that we can easily interchange the logos attached into. The presentation will be used for general company sales information. The group is called VeraMosk and has 2 companies, k7datagrove and Copper Thread. We're an IT services company who specialises in Broadband and general network services.

Target Market(s)

Professional

```html
<!DOCTYPE html>
<html lang="en">
<head>
<meta charset="utf-8">
<title>VeraMosk Group Presentation</title>
<link href="https://fonts.googleapis.com/css2?family=Poppins:wght@400;500;600;700&display=swap" rel="stylesheet">
<style>
:root{
  --page:#eef3f7;
  --deep-green:#17803d;
  --leaf-green:#8dc63f;
  --pale-green:#c9e6a6;
  --sky-blue:#29a8e0;
  --signal-red:#d0021b;
  --ink:#2b2b2b;
  --body-text:#6b6b6b;
  --cream:#efece0;
  --white:#ffffff;
}
*{box-sizing:border-box;margin:0;padding:0}
html,body{width:1200px;height:4051px;overflow:hidden}
body{background:var(--page);font-family:'Poppins',sans-serif;position:relative;color:var(--ink)}
.slide{position:absolute;left:75px;width:1048px;height:588px;background:var(--white);overflow:hidden;box-shadow:0 4px 14px rgba(0,0,0,.08)}
.abs{position:absolute}
.brand{position:absolute;display:flex;align-items:center;gap:8px;font-weight:500;color:var(--ink)}
.brand .dot{width:22px;height:22px;border-radius:50%;background:var(--deep-green)}
.brand-main{font-size:30px;top:34px;right:58px}
.brand-main .dot{width:26px;height:26px}
.partners{position:absolute;top:531px;left:592px;display:flex;align-items:center;gap:22px;font-size:19px;font-weight:500;color:var(--ink)}
.partner{display:flex;align-items:center;gap:6px}
.partner .dot{width:16px;height:16px;border-radius:50%;background:var(--deep-green)}
.partner.k7 .dot{background:var(--signal-red)}
.red-dot{width:17px;height:17px;border-radius:50%;background:var(--signal-red);margin-left:6px}
.footer-bar{position:absolute;left:0;top:531px;width:560px;height:32px;background:var(--sky-blue);border-radius:0 16px 16px 0}
.header-band{position:absolute;left:0;top:0;width:700px;height:90px}
.slide-title{position:absolute;left:61px;top:20px;font-size:31px;font-weight:600;color:var(--white);letter-spacing:.3px}
.photo{position:absolute;border-radius:20px}
.copy{font-size:12.5px;line-height:21px;color:var(--body-text);text-align:justify}
.copy p+p{margin-top:15px}
.welcome-kicker{left:616px;top:178px;font-size:22px;font-weight:500;color:var(--deep-green)}
.welcome-title{left:616px;top:205px;font-size:38px;font-weight:600;color:var(--leaf-green)}
.welcome-rule{left:616px;top:257px;width:95px;height:3px;background:var(--sky-blue)}
.welcome-copy{left:616px;top:290px;width:373px;font-size:14px;line-height:24.5px;color:#3a3a3a;text-align:justify}
.service-card{position:absolute;top:192px;width:299px;height:280px;border:2px solid var(--deep-green);border-radius:16px;text-align:center;padding:80px 20px 0}
.service-card.light{border-color:var(--leaf-green)}
.icon-disc{position:absolute;border-radius:50%;display:flex;align-items:center;justify-content:center}
.service-card .icon-disc{width:91px;height:91px;left:102px;top:-46px;background:var(--deep-green)}
.service-card.light .icon-disc{background:var(--leaf-green)}
.card-heading{font-size:17px;font-weight:600;color:#333;margin-bottom:14px}
.card-copy{font-size:12.5px;line-height:23px;color:var(--body-text)}
.benefits{left:61px;top:155px;width:440px;list-style:none}
.benefits li{position:relative;padding-left:33px;font-size:12.5px;line-height:21px;color:var(--body-text);margin-bottom:11px}
.benefits li::before{content:"";position:absolute;left:0;top:5px;width:11px;height:11px;border-radius:50%;background:var(--deep-green)}
.why-card{position:absolute;top:165px;width:213px;height:286px;border-radius:12px;background:var(--white);box-shadow:0 2px 10px rgba(0,0,0,.12);text-align:center;padding:137px 14px 0}
.why-card .icon-disc{width:76px;height:76px;left:68px;top:27px;background:var(--deep-green)}
.why-card.light .icon-disc{background:var(--leaf-green)}
.why-card .card-heading{font-size:14px;margin-bottom:8px}
.why-card .card-copy{font-size:11.5px;line-height:21px}
.thanks{left:61px;top:160px;font-size:47px;font-weight:700;color:var(--deep-green)}
.thanks span{color:var(--leaf-green)}
.contacts{left:61px;top:285px;list-style:none}
.contacts li{display:flex;align-items:flex-start;gap:22px;font-size:16px;font-weight:500;color:var(--ink);line-height:22px;margin-bottom:23px}
.contacts svg{flex:none;width:32px;height:26px}
</style>
</head>
<body>

<svg width="0" height="0" style="position:absolute">
  <defs>
    <linearGradient id="bandFill" x1="0" x2="1" y1="0" y2="0">
      <stop offset="0" stop-color="#17803d"/><stop offset=".55" stop-color="#3ea23a"/><stop offset="1" stop-color="#8dc63f"/>
    </linearGradient>
  </defs>
</svg>

<!-- Slide 1: Welcome -->
<section class="slide" style="top:88px;background:var(--cream)">
  <div class="abs" role="img" aria-label="City skyline at dusk blended into a head profile with network connection icons" style="left:0;top:0;width:600px;height:588px;background:linear-gradient(90deg,#3d4a4e 0%,#6f8085 45%,#a9b2ad 75%,rgba(239,236,224,0) 100%)"></div>
  <div class="brand brand-main"><span class="dot"></span>VeraMosk</div>
  <div class="abs welcome-kicker">WELCOME TO</div>
  <div class="abs welcome-title">VERAMOSK GROUP</div>
  <div class="abs welcome-rule"></div>
  <p class="abs welcome-copy">Lorem ipsum dolor sit amet, consectetur adipiscing elit, sed do eiusm od tempor incididunt ut labore et dolore magna aliqua. Ut enim ad minim veniam, quis nostrud exercitation ullamco laboris nisi ut aliquip ex ea commodo consequat.</p>
  <div class="partners"><span class="partner"><span class="dot"></span>Copper Thread</span><span class="partner k7"><span class="dot"></span>k7datagrove</span><span class="red-dot"></span></div>
</section>

<!-- Slide 2: About -->
<section class="slide" style="top:738px">
  <svg class="header-band" viewBox="0 0 700 90"><polygon points="0,0 648,0 604,82 0,82" fill="url(#bandFill)"/><polygon points="604,82 648,0 654,0 610,90 0,90 0,82" fill="var(--pale-green)"/></svg>
  <div class="slide-title">ABOUT US</div>
  <div class="brand brand-main"><span class="dot"></span>VeraMosk</div>
  <div class="photo" role="img" aria-label="Two engineers reviewing a tablet in a server room" style="left:66px;top:127px;width:458px;height:359px;background:linear-gradient(135deg,#5b87b8 0%,#2d3f5c 55%,#1b2333 100%)"></div>
  <div class="abs copy" style="left:585px;top:170px;width:403px">
    <p>Lorem ipsum dolor sit amet, consectetur adipiscing elit, sed do eiusmod tempor incididunt ut labore et dolore magna aliqua. Ut enim ad minim veniam, quis nostrud exercitation ullamco laboris nisi ut aliquip ex ea commodo consequat.</p>
    <p>Consectetur adipiscing elit, sed do eiusmod tempor incididunt ut labore et dolore magna aliqua. Ut enim ad minim veniam, quis nostrud exercitation ullamcoea.</p>
    <p>Duis aute irure dolor in reprehenderit in voluptate velit esse cillum dolore eu fugiat nulla pariatur. Excepteur sint occaecat cupidatat non proident, sunt in culpa qui officia deserunt mollit anim id est labodolor in in voluptaterum.</p>
  </div>
  <div class="footer-bar"></div>
  <div class="partners"><span class="partner"><span class="dot"></span>Copper Thread</span><span class="partner k7"><span class="dot"></span>k7datagrove</span><span class="red-dot"></span></div>
</section>

<!-- Slide 3: Services -->
<section class="slide" style="top:1397px">
  <svg class="header-band" viewBox="0 0 700 90"><polygon points="0,0 648,0 604,82 0,82" fill="url(#bandFill)"/><polygon points="604,82 648,0 654,0 610,90 0,90 0,82" fill="var(--pale-green)"/></svg>
  <div class="slide-title">OUR SERVICES</div>
  <div class="brand brand-main"><span class="dot"></span>VeraMosk</div>
  <div class="service-card" style="left:209px">
    <div class="icon-disc"><svg width="46" height="40" viewBox="0 0 46 40" fill="none" stroke="#fff" stroke-width="2"><rect x="4" y="24" width="34" height="10" rx="2"/><line x1="34" y1="24" x2="34" y2="6"/><path d="M10 16a12 12 0 0 1 16 0M13 19a7 7 0 0 1 10 0"/><circle cx="10" cy="29" r="1.2" fill="#fff"/><circle cx="15" cy="29" r="1.2" fill="#fff"/><circle cx="20" cy="29" r="1.2" fill="#fff"/></svg></div>
    <div class="card-heading">BROADBAND</div>
    <p class="card-copy">Lorem ipsum dolor sit amet, consectetur adipiscing elit, sed do eiusmod tempor incididunt ut labore et dolore magna aliqua. Ut enim ad minim veniam, quis nostrud exercitation ullamco laboris nisi ut aliquip ex ea commodoea.</p>
  </div>
  <div class="service-card light" style="left:540px">
    <div class="icon-disc"><svg width="44" height="44" viewBox="0 0 44 44" fill="none" stroke="#fff" stroke-width="2"><circle cx="22" cy="22" r="17"/><ellipse cx="22" cy="22" rx="7" ry="17"/><line x1="5" y1="22" x2="39" y2="22"/></svg></div>
    <div class="card-heading">GENERAL NETWORK</div>
    <p class="card-copy">Lorem ipsum dolor sit amet, consectetur adipiscing elit, sed do eiusmod tempor incididunt ut labore et dolore magna aliqua. Ut enim ad minim veniam, quis nostrud exercitation ullamco laboris nisi ut aliquip ex ea commodoea.</p>
  </div>
  <div class="footer-bar"></div>
  <div class="partners"><span class="partner"><span class="dot"></span>Copper Thread</span><span class="partner k7"><span class="dot"></span>k7datagrove</span><span class="red-dot"></span></div>
</section>

<!-- Slide 4: Benefits -->
<section class="slide" style="top:2056px">
  <svg class="header-band" viewBox="0 0 700 90"><polygon points="0,0 648,0 604,82 0,82" fill="url(#bandFill)"/><polygon points="604,82 648,0 654,0 610,90 0,90 0,82" fill="var(--pale-green)"/></svg>
  <div class="slide-title">OUR BENEFITS</div>
  <div class="brand brand-main"><span class="dot"></span>VeraMosk</div>
  <ul class="abs benefits">
    <li>Lorem ipsum dolor sit amet, consectetur adipiscing elit, sed do eiusmod tempor incididunt ut labore et dolore magna aliqua. Ut enim ad minim veniam.</li>
    <li>Consectetur adipiscing elit, sed do eiusmod tempor incididunt ut labore et dolore magna aliqua.</li>
    <li>Lorem ipsum dolor sit amet, consectetur adipiscing elit, sed do eiusmod tempor incididunt ut labore et dolore magna aliqua. Ut enim ad minim veniam.</li>
    <li>Consectetur adipiscing elit, sed do eiusmod tempor incididunt ut labore et dolore magna aliqua.</li>
    <li>Lorem ipsum dolor sit amet, consectetur adipiscing elit, sed do eiusmod tempor incididunt ut labore et dolore magna aliqua. Ut enim ad minim veniam.</li>
  </ul>
  <div class="photo" role="img" aria-label="Digital globe made of glowing binary data" style="left:530px;top:132px;width:458px;height:354px;background:radial-gradient(circle at 70% 55%,#3f7ea3 0%,#1d3d5e 40%,#0c1a2e 80%)"></div>
  <div class="footer-bar"></div>
  <div class="partners"><span class="partner"><span class="dot"></span>Copper Thread</span><span class="partner k7"><span class="dot"></span>k7datagrove</span><span class="red-dot"></span></div>
</section>

<!-- Slide 5: Why choose us -->
<section class="slide" style="top:2715px">
  <svg class="header-band" viewBox="0 0 700 90"><polygon points="0,0 648,0 604,82 0,82" fill="url(#bandFill)"/><polygon points="604,82 648,0 654,0 610,90 0,90 0,82" fill="var(--pale-green)"/></svg>
  <div class="slide-title">WHY CHOOSE US</div>
  <div class="brand brand-main"><span class="dot"></span>VeraMosk</div>
  <div class="why-card" style="left:61px">
    <div class="icon-disc"><svg width="38" height="38" viewBox="0 0 38 38" fill="none" stroke="#fff" stroke-width="2"><circle cx="19" cy="19" r="13"/><ellipse cx="19" cy="19" rx="5" ry="13"/><line x1="6" y1="19" x2="32" y2="19"/></svg></div>
    <div class="card-heading">LOREM IPSUM</div>
    <p class="card-copy">Lorem ipsum dolor sit amet, co nsectetur adipiscing elit, sed do eiusmod tempor incididunt ut labore et dolore magna aliqua ut enim ad minea.</p>
  </div>
  <div class="why-card light" style="left:299px">
    <div class="icon-disc"><svg width="38" height="38" viewBox="0 0 38 38" fill="none" stroke="#fff" stroke-width="2"><circle cx="12" cy="12" r="5"/><circle cx="26" cy="12" r="5"/><circle cx="12" cy="26" r="5"/><circle cx="26" cy="26" r="5"/></svg></div>
    <div class="card-heading">LOREM IPSUM</div>
    <p class="card-copy">Lorem ipsum dolor sit amet, co nsectetur adipiscing elit, sed do eiusmod tempor incididunt ut labore et dolore magna aliqua ut enim ad minea.</p>
  </div>
  <div class="why-card" style="left:536px">
    <div class="icon-disc"><svg width="38" height="38" viewBox="0 0 38 38" fill="none" stroke="#fff" stroke-width="2"><rect x="12" y="6" width="14" height="10" rx="2"/><line x1="19" y1="16" x2="19" y2="22"/><line x1="8" y1="22" x2="30" y2="22"/><rect x="4" y="25" width="8" height="7"/><rect x="15" y="25" width="8" height="7"/><rect x="26" y="25" width="8" height="7"/></svg></div>
    <div class="card-heading">LOREM IPSUM</div>
    <p class="card-copy">Lorem ipsum dolor sit amet, co nsectetur adipiscing elit, sed do eiusmod tempor incididunt ut labore et dolore magna aliqua ut enim ad minea.</p>
  </div>
  <div class="why-card light" style="left:775px">
    <div class="icon-disc"><svg width="38" height="38" viewBox="0 0 38 38" fill="none" stroke="#fff" stroke-width="2"><rect x="5" y="7" width="12" height="10" rx="2"/><rect x="21" y="7" width="12" height="10" rx="2"/><rect x="5" y="21" width="12" height="10" rx="2"/><rect x="21" y="21" width="12" height="10" rx="2"/></svg></div>
    <div class="card-heading">LOREM IPSUM</div>
    <p class="card-copy">Lorem ipsum dolor sit amet, co nsectetur adipiscing elit, sed do eiusmod tempor incididunt ut labore et dolore magna aliqua ut enim ad minea.</p>
  </div>
  <div class="footer-bar"></div>
  <div class="partners"><span class="partner"><span class="dot"></span>Copper Thread</span><span class="partner k7"><span class="dot"></span>k7datagrove</span><span class="red-dot"></span></div>
</section>

<!-- Slide 6: Thank you -->
<section class="slide" style="top:3373px">
  <svg class="abs" style="left:0;top:0" width="1048" height="588" viewBox="0 0 1048 588">
    <defs>
      <linearGradient id="skyFill" x1="0" x2="1" y1="0" y2="1">
        <stop offset="0" stop-color="#2c4f7a"/><stop offset=".5" stop-color="#8fb9d8"/><stop offset="1" stop-color="#1e3550"/>
      </linearGradient>
    </defs>
    <polygon role="img" aria-label="Businessman looking at a city skyline under a glowing global network" points="417,0 1048,0 1048,588 664,588" fill="url(#skyFill)"/>
    <polygon points="546,315 459,588 664,588" fill="var(--signal-red)"/>
  </svg>
  <div class="brand" style="left:61px;top:36px;font-size:30px"><span class="dot" style="width:26px;height:26px"></span>VeraMosk</div>
  <div class="abs thanks">THANK <span>YOU</span></div>
  <ul class="abs contacts">
    <li><svg viewBox="0 0 32 26"><path d="M8 3l5 5-3 3c2 4 5 7 9 9l3-3 5 5-4 3C13 24 6 16 5 7z" fill="var(--sky-blue)"/></svg>+1 (555) 214 7390</li>
    <li><svg viewBox="0 0 32 26" fill="none" stroke="var(--sky-blue)" stroke-width="2"><circle cx="16" cy="13" r="11"/><ellipse cx="16" cy="13" rx="4.5" ry="11"/><line x1="5" y1="13" x2="27" y2="13"/></svg>https://www.veramosk.com/</li>
    <li><svg viewBox="0 0 32 26"><rect x="3" y="4" width="26" height="18" fill="var(--sky-blue)"/><path d="M3 4l13 11L29 4" fill="none" stroke="#fff" stroke-width="2"/></svg>info@veramosk.com</li>
    <li><svg viewBox="0 0 32 26"><path d="M16 1a8 8 0 0 1 8 8c0 6-8 12-8 12S8 15 8 9a8 8 0 0 1 8-8z" fill="var(--sky-blue)"/><circle cx="16" cy="9" r="3" fill="#fff"/><ellipse cx="16" cy="23" rx="8" ry="2" fill="var(--sky-blue)"/></svg><span>218, Harlow Crest Avenue,<br>United States</span></li>
  </ul>
  <div class="partners" style="left:61px"><span class="partner"><span class="dot"></span>Copper Thread</span><span class="partner k7"><span class="dot"></span>k7datagrove</span></div>
</section>

</body>
</html>
```